Design a building access mobile app for Quillo by Tamberlin Entry Systems

Hello, We're looking for an awesome designer to create an app design for our app Quillo, by Tamberlin Entry Systems. the mobile app allows employees open their office doors with their mobile phone. this means they don't have to use those plastic card badges or keys. We like clean modern design, dark and light themes. We don't have a logo yet.
Updates

Reason: Waiting on a couple designers to submit concepts

Target Market(s)

Commercial and employees

Industry/Entity Type

Building

Font styles to use
Sans Serif
Other font styles liked:
• Oswald extra light

Requirements
Must have
• nice clean design

```html
<!DOCTYPE html>
<html lang="en">
<head>
<meta charset="utf-8">
<title>Quillo – Sign Up</title>
<link href="https://fonts.googleapis.com/css2?family=Oswald:wght@200;300;400;500;600&family=Roboto:wght@400&display=swap" rel="stylesheet">
<style>
  :root {
    --sky: #86e3fa;
    --sky-deep: #7cd8f0;
    --teal: #2d8ba5;
    --teal-dark: #23667a;
    --teal-soft: #3b8fa8;
    --field: rgba(120, 214, 238, 0.55);
    --field-edge: rgba(70, 160, 190, 0.35);
    --status: #5c7a85;
    --white: #ffffff;
  }
  * { box-sizing: border-box; margin: 0; padding: 0; }
  html, body { width: 675px; height: 1200px; overflow: hidden; }
  body { font-family: "Oswald", sans-serif; background: var(--sky); }

  .screen { position: relative; width: 675px; height: 1200px; overflow: hidden; }

  .backdrop {
    position: absolute; inset: 0;
    background: linear-gradient(160deg, #8fe7fb 0%, var(--sky) 45%, var(--sky-deep) 100%);
  }

  .status-bar {
    position: absolute; top: 0; left: 0; right: 0; height: 40px;
    font-family: "Roboto", sans-serif; font-size: 15px; color: var(--status);
  }
  .status-bar .signal { position: absolute; left: 10px; top: 12px; }
  .status-bar .time { position: absolute; left: 0; right: 0; top: 11px; text-align: center; }
  .status-bar .battery { position: absolute; right: 10px; top: 11px; display: flex; align-items: center; gap: 4px; }

  .brand-mark {
    position: absolute; left: 282px; top: 170px; width: 110px; height: 110px;
    background: var(--teal); border-radius: 6px;
  }
  .brand-name {
    position: absolute; left: 0; right: 0; top: 338px; text-align: center;
    font-size: 44px; font-weight: 400; color: var(--teal-dark); letter-spacing: 0.3px;
  }

  .page-title {
    position: absolute; left: 0; right: 0; top: 458px; text-align: center;
    font-size: 38px; font-weight: 200; color: var(--teal-soft);
  }
  .page-title span { border-bottom: 1px solid var(--teal-soft); padding-bottom: 1px; }

  .field {
    position: absolute; left: 50px; width: 576px; height: 72px;
    background: var(--field); border-radius: 4px;
    box-shadow: 0 2px 2px rgba(40, 120, 150, 0.18);
    display: flex; align-items: center; padding: 0 20px 0 23px;
    font-size: 32px; font-weight: 300; color: #5d98a8;
  }
  .field .value { flex: 1; color: #23505e; }
  .field .value::after {
    content: ""; display: inline-block; width: 1px; height: 40px;
    background: #3057c9; vertical-align: middle; margin-left: 4px;
  }
  .field .placeholder { flex: 1; }
  .field--active { border: 1px solid var(--field-edge); box-shadow: none; }
  .field--email { top: 593px; }
  .field--password { top: 686px; }
  .field--confirm { top: 778px; }

  .toggle {
    position: absolute; left: 53px; top: 886px; display: flex; align-items: center; gap: 17px;
    font-size: 31px; font-weight: 300; color: var(--teal-dark);
  }

  .register-button {
    position: absolute; left: 50px; top: 978px; width: 576px; height: 72px;
    background: var(--teal); border-radius: 4px;
    box-shadow: 0 2px 3px rgba(30, 90, 110, 0.3);
    display: flex; align-items: center; justify-content: center;
    color: var(--white); font-size: 34px; font-weight: 500;
  }

  .login-prompt {
    position: absolute; left: 0; right: 0; top: 1116px; text-align: center;
    font-size: 30px; font-weight: 200; color: var(--teal-soft);
  }
  .login-prompt .login-link {
    font-weight: 300; color: var(--teal); border-bottom: 1px solid var(--teal);
  }
</style>
</head>
<body>
<main class="screen">
  <div class="backdrop" role="img" aria-label="Soft, faded office hallway photo under a light cyan tint"></div>

  <header class="status-bar">
    <svg class="signal" width="70" height="14" viewBox="0 0 70 14" aria-hidden="true">
      <g fill="var(--status)">
        <circle cx="5" cy="7" r="4"/><circle cx="15" cy="7" r="4"/><circle cx="25" cy="7" r="4"/>
        <circle cx="35" cy="7" r="4"/><circle cx="45" cy="7" r="4"/>
      </g>
      <g fill="none" stroke="var(--status)" stroke-width="2" stroke-linecap="round">
        <path d="M54 6 a9 9 0 0 1 12 0"/><path d="M57 9 a5 5 0 0 1 6 0"/>
      </g>
      <circle cx="60" cy="12" r="1.6" fill="var(--status)"/>
    </svg>
    <div class="time">9:41 PM</div>
    <div class="battery">
      <svg width="9" height="15" viewBox="0 0 9 15" aria-hidden="true"><path d="M1 4 L8 10 L4.5 13 V1 L8 4 L1 10" fill="none" stroke="var(--status)" stroke-width="1.3"/></svg>
      <span>100%</span>
      <svg width="30" height="14" viewBox="0 0 30 14" aria-hidden="true">
        <rect x="0.5" y="0.5" width="26" height="13" rx="2" fill="none" stroke="var(--status)"/>
        <rect x="2" y="2" width="23" height="10" rx="1" fill="var(--status)"/>
        <rect x="27.5" y="4.5" width="2" height="5" rx="1" fill="var(--status)"/>
      </svg>
    </div>
  </header>

  <div class="brand-mark" aria-hidden="true"></div>
  <h1 class="brand-name">Tamberlin security</h1>

  <h2 class="page-title"><span>Sign Up</span></h2>

  <div class="field field--email field--active">
    <span class="value">maraquint@example.com</span>
    <svg width="36" height="28" viewBox="0 0 36 28" aria-hidden="true">
      <rect x="0" y="0" width="36" height="28" rx="2" fill="var(--teal)"/>
      <path d="M2 3 L18 16 L34 3" fill="none" stroke="var(--sky)" stroke-width="2.5"/>
      <path d="M2 26 L13 13 M34 26 L23 13" stroke="var(--sky)" stroke-width="2"/>
    </svg>
  </div>

  <div class="field field--password">
    <span class="placeholder">Password</span>
    <svg width="30" height="40" viewBox="0 0 30 40" aria-hidden="true">
      <path d="M7 17 V11 a8 8 0 0 1 16 0 V17" fill="none" stroke="var(--teal)" stroke-width="4"/>
      <rect x="1" y="16" width="28" height="23" rx="4" fill="var(--teal)"/>
      <circle cx="15" cy="25" r="3" fill="var(--sky)"/><rect x="14" y="26" width="2" height="7" fill="var(--sky)"/>
    </svg>
  </div>

  <div class="field field--confirm">
    <span class="placeholder">Confirm Password</span>
    <svg width="30" height="40" viewBox="0 0 30 40" aria-hidden="true">
      <path d="M7 17 V11 a8 8 0 0 1 16 0 V17" fill="none" stroke="var(--teal)" stroke-width="4"/>
      <rect x="1" y="16" width="28" height="23" rx="4" fill="var(--teal)"/>
      <circle cx="15" cy="25" r="3" fill="var(--sky)"/><rect x="14" y="26" width="2" height="7" fill="var(--sky)"/>
    </svg>
  </div>

  <label class="toggle">
    <svg width="33" height="33" viewBox="0 0 33 33" aria-hidden="true">
      <rect x="1.5" y="1.5" width="30" height="30" rx="3" fill="none" stroke="var(--teal-dark)" stroke-width="2.5"/>
      <path d="M8 17 L14 23 L26 9" fill="none" stroke="var(--teal-dark)" stroke-width="2"/>
    </svg>
    <span>Enable Touch</span>
  </label>

  <div class="register-button">Register</div>

  <p class="login-prompt">Already have an account? <span class="login-link">LOGIN</span> now</p>
</main>
</body>
</html>
```